Lorvex Tilo medical cannibis cultivation company

tag - Tilo rise
Lorvex Tilo medical cannabis cultivation - logo is selected- can we please see bold examples with our selection. We are mainly dealing with medical companies and professionals. We would like to be stand out in the crowd with our designs. Welcome any and all attempts. Thanks

Target Market(s)

Medical and Professional

Industry/Entity Type

Medical And Science

Font styles to use
Sans Serif

Colors

Designer to choose colors to be used in the design.

Requirements
Must have
• Bright colour and be bold- Love the teal and magenta that is currently on the dark background design.
Nice to have
• shading and the 3D affect- The shadowed appearance.
Should not have
• Anything related to illegal activity or un professional manners

```html
<!DOCTYPE html>
<html lang="en">
<head>
<meta charset="utf-8">
<title>Lorvex Tilo – Business Card</title>
<link rel="stylesheet" href="https://fonts.googleapis.com/css2?family=Roboto:wght@400;500;700&display=swap">
<style>
  :root {
    --stage: #e8e3da;
    --card: #050505;
    --teal: #00a9e2;
    --magenta: #9b4aa0;
    --grey: #8e9095;
    --white: #ffffff;
  }
  * { margin: 0; padding: 0; box-sizing: border-box; }
  html, body {
    width: 1200px; height: 1040px; overflow: hidden;
    background: var(--stage);
    font-family: "Roboto", Arial, sans-serif;
  }
  .canvas { position: relative; width: 1200px; height: 1040px; }
  .card {
    position: absolute; left: 250px; width: 700px; height: 400px;
    background: var(--card); border-radius: 26px; overflow: hidden;
    box-shadow: 0 14px 28px rgba(0,0,0,.35), 0 4px 0 #0b7fa8;
  }
  .card--front { top: 70px; }
  .card--back { top: 570px; box-shadow: 0 14px 28px rgba(0,0,0,.35); }
  .front-band { position: absolute; inset: 0; }

  .brand { position: absolute; left: 36px; top: 96px; width: 250px; text-align: center; }
  .brand-ring {
    width: 110px; height: 110px; margin: 0 auto 20px;
    border: 5px solid var(--grey); border-radius: 50%;
  }
  .brand-name {
    color: var(--teal); font-weight: 500; font-size: 36px;
    text-transform: uppercase; letter-spacing: 1px; white-space: nowrap;
  }
  .brand-tag {
    display: flex; align-items: center; gap: 8px; justify-content: center;
    color: var(--grey); font-size: 16px; letter-spacing: 3px; text-transform: uppercase; margin-top: 4px;
  }
  .brand-tag::before, .brand-tag::after { content: ""; flex: 1; height: 1px; background: var(--grey); }

  .contact { position: absolute; left: 318px; top: 52px; color: var(--white); }
  .contact-name { color: var(--teal); font-weight: 700; font-size: 27px; text-transform: uppercase; }
  .contact-role { color: var(--magenta); font-size: 18px; text-transform: uppercase; margin-bottom: 14px; }
  .contact-address { font-size: 17px; line-height: 23px; margin-bottom: 12px; }
  .contact-list { list-style: none; font-size: 17px; line-height: 23px; }
  .contact-list li { display: flex; align-items: center; gap: 9px; }
  .contact-list svg { width: 14px; height: 14px; flex: none; }

  .back-url {
    position: absolute; left: 70px; top: 200px; transform-origin: 0 0; transform: rotate(90deg) translate(-50%, 0);
    color: var(--white); font-size: 17px; letter-spacing: 5px; white-space: nowrap;
  }
  .back-brand { position: absolute; left: 250px; top: 90px; width: 320px; text-align: center; }
  .back-brand .brand-ring { width: 130px; height: 130px; }
</style>
</head>
<body>
<main class="canvas">
  <section class="card card--front">
    <svg class="front-band" viewBox="0 0 700 400" aria-hidden="true">
      <path d="M330 400 Q640 360 700 60 L700 400 Z" fill="var(--teal)"/>
      <path d="M300 404 Q628 352 690 0" fill="none" stroke="var(--magenta)" stroke-width="5"/>
    </svg>

    <div class="brand">
      <div class="brand-ring"></div>
      <div class="brand-name">Lorvex Tilo</div>
      <div class="brand-tag">Tilo rise</div>
    </div>

    <div class="contact">
      <div class="contact-name">Maren Ostlund</div>
      <div class="contact-role">CEO/Founder</div>
      <div class="contact-address">4120 Quillfield Road<br>Harrowgate, Vermont 21908</div>
      <ul class="contact-list">
        <li><svg viewBox="0 0 14 14"><path d="M3 1 L5.5 4 L4 5.5 Q5.5 8.5 8.5 10 L10 8.5 L13 11 L11 13 Q3 11 1 3 Z" fill="var(--teal)"/></svg>555 214 7730</li>
        <li><svg viewBox="0 0 14 14"><rect x="3.5" y="1" width="7" height="12" rx="1.5" fill="none" stroke="var(--teal)" stroke-width="1.6"/></svg>555 809 3316</li>
        <li><svg viewBox="0 0 14 14"><rect x="2" y="5" width="10" height="7" fill="var(--teal)"/><rect x="4" y="1.5" width="6" height="4" fill="none" stroke="var(--teal)" stroke-width="1.4"/></svg>555 362 0481</li>
        <li><svg viewBox="0 0 14 14"><rect x="1" y="3" width="12" height="8" fill="var(--teal)"/><path d="M1 3 L7 8 L13 3" fill="none" stroke="var(--card)" stroke-width="1.2"/></svg>maren@lorvextilo.com</li>
        <li><svg viewBox="0 0 14 14"><circle cx="7" cy="7" r="6" fill="var(--teal)"/><path d="M1 7 H13 M7 1 Q3 7 7 13 Q11 7 7 1" fill="none" stroke="var(--card)" stroke-width="1"/></svg>www.lorvextilo.com</li>
      </ul>
    </div>
  </section>

  <section class="card card--back">
    <div class="back-url">www.lorvextilorise.com</div>
    <div class="back-brand">
      <div class="brand-ring"></div>
      <div class="brand-name">Lorvex Tilo</div>
    </div>
  </section>
</main>
</body>
</html>
```